Les Brumevents

I need a book cover for an action series. Two books are already on sale, but the covers have been rejected by some online booksellers for having a shirtless man on the cover.
https://www.bookvane.com/dp/Q58KT2R7WX

The Bookvane pages give descriptions of the book. I'm taking bids on modification of the first book, but the intention would be to use the same designer for the series.

Timeline for delivery is ideally end of Q1 22 for cover

My goal for the coves is for the reader to see some kind of "hook" that makes them intrigued enough to click the link. The cover will need to convey the genre of the book (action thriller) and give the potential buyer a reason to click for more information. Some online booksellers only show cover and title, so the cover needs to sell the book.

The actual gender split in the mystery-thriller field has faded, and the cover shouldn't just appeal to men although the gender spilt is still 60-40 towards male readership.

In the initial design, I was attempting to use country/continental outlines to convey as sense of "International Thriller", as the main character is an ex-French Foreign Legionnaire.

I would like to prioritize these elements:
Title
Series Name & Number

The author name doesn't need to be prominent or even on the front cover. Back cover copy is available, on the Bookvane description, but I can resend as text.

Target Market(s)

Requirements
Must have
• Title & Series Name & Number
Should not have
• Nudity, or explicit sexual content

```html
<!DOCTYPE html>
<html lang="en">
<head>
<meta charset="utf-8">
<title>Saharan Evacuation – Les Brumevents – Cover Wrap</title>
<link rel="stylesheet" href="https://fonts.googleapis.com/css2?family=Bebas+Neue&family=Oswald:wght@200&family=Archivo+Black&family=Montserrat:wght@800&family=Roboto:wght@400&display=swap">
<style>
  :root {
    --stage: #ffffff;
    --cover-black: #000000;
    --spine-black: #050505;
    --title-white: #ffffff;
    --accent-red: #e3161b;
    --body-grey: #e6e6e6;
    --photo-light: #bdbdb8;
    --photo-mid: #4a4a48;
  }
  * { margin: 0; padding: 0; box-sizing: border-box; }
  html, body { width: 1200px; height: 288px; overflow: hidden; background: var(--stage); }
  .stage { position: relative; width: 1200px; height: 288px; display: flex; justify-content: center; }
  .wrap { position: relative; width: 420px; height: 288px; background: var(--cover-black); display: flex; }

  .back-cover { position: relative; width: 193px; height: 288px; }
  .spine { position: relative; width: 35px; height: 288px; background: var(--spine-black); }
  .front-cover { position: relative; width: 192px; height: 288px; overflow: hidden; }

  .series-name { font-family: "Oswald", sans-serif; font-weight: 200; color: var(--title-white); text-transform: uppercase; text-align: center; }
  .title-red { font-family: "Archivo Black", sans-serif; font-weight: 400; color: var(--accent-red); text-transform: uppercase; text-align: center; line-height: 1; }
  .title-white { font-family: "Bebas Neue", sans-serif; font-weight: 400; color: var(--title-white); text-transform: uppercase; text-align: center; line-height: 0.9; }
  .author { font-family: "Montserrat", sans-serif; font-weight: 800; color: var(--title-white); text-transform: uppercase; text-align: center; }

  .back-title { position: absolute; top: 44px; left: 0; width: 193px; }
  .back-title .title-red { font-size: 12px; letter-spacing: 5px; padding-left: 5px; }
  .back-title .title-white { font-size: 23px; margin-top: 2px; }
  .back-title .series-name { font-size: 12.5px; line-height: 1; margin-top: 1px; letter-spacing: 0.3px; }

  .blurb { position: absolute; top: 99px; left: 18px; width: 157px; font-family: "Roboto", sans-serif; font-size: 5.2px; line-height: 8.9px; color: var(--body-grey); text-align: justify; text-align-last: center; }
  .blurb p + p { margin-top: 9px; }

  .spine-column { position: absolute; writing-mode: vertical-rl; white-space: nowrap; }
  .spine-title { top: 13px; left: 12px; display: flex; align-items: center; }
  .spine-title .title-red { font-size: 11px; letter-spacing: 3px; }
  .spine-title .title-white { font-size: 13px; margin-top: 4px; letter-spacing: 0.3px; }
  .spine-series { left: 3px; top: 53px; font-size: 8.5px; letter-spacing: 0.3px; }
  .spine-author { left: 13px; top: 204px; font-size: 7.5px; letter-spacing: 1.5px; }

  .front-series { position: absolute; top: 19px; left: 0; width: 192px; font-size: 24px; line-height: 1; letter-spacing: 0.5px; }
  .front-title { position: absolute; top: 47px; left: 0; width: 192px; font-weight: 400; }
  .front-title .title-red { font-size: 21px; letter-spacing: 8px; padding-left: 8px; }
  .front-title .title-white { font-size: 41px; margin-top: 3px; }

  .cover-photo { position: absolute; top: 112px; left: 0; width: 192px; height: 136px;
    background: radial-gradient(ellipse 42% 48% at 48% 52%, var(--photo-light) 0%, var(--photo-mid) 45%, var(--cover-black) 100%); }

  .front-author { position: absolute; top: 257px; left: 0; width: 192px; font-size: 12.5px; letter-spacing: 1.2px; }
</style>
</head>
<body>
<main class="stage">
  <section class="wrap" aria-label="Book cover wrap: Saharan Evacuation">
    <div class="back-cover">
      <header class="back-title">
        <div class="title-red">Saharan</div>
        <div class="title-white">Evacuation</div>
        <div class="series-name">Les Brumevents</div>
      </header>
      <div class="blurb">
        <p>Lorem ipsum dolor sit amet, consectetur adipiscing elit, sed do eiusmod tempor incididunt ut labore et dolore magna aliqua. Quis ipsum suspendisse ultrices gravida. Risus commodo viverra maecenas accumsan lacus vel facilisis. Lorem ipsum dolor sit amet, consectetur adipiscing elit, sed do eiusmod tempor incididunt ut labore et dolore magna aliqua. Quis ipsum suspendisse ultrices gravida. Risus commodo viverra maecenas accumsan lacus vel facilisis.</p>
        <p>Lorem ipsum dolor sit amet, consectetur adipiscing elit, sed do eiusmod tempor incididunt ut labore et dolore magna aliqua. Quis ipsum suspendisse ultrices gravida. Risus commodo viverra maecenas accumsan lacus vel facilisis. Lorem ipsum dolor sit amet, consectetur adipiscing elit, sed do eiusmod tempor incididunt ut labore et dolore magna aliqua. Quis ipsum suspendisse ultrices gravida. Risus commodo viverra maecenas accumsan lacus vel facilisis.</p>
      </div>
    </div>

    <div class="spine">
      <div class="spine-column spine-series series-name">Les Brumevents</div>
      <div class="spine-column spine-title">
        <span class="title-red">Saharan</span>
        <span class="title-white">Evacuation</span>
      </div>
      <div class="spine-column spine-author author">Marc Delorne</div>
    </div>

    <div class="front-cover">
      <div class="front-series series-name">Les Brumevents</div>
      <h1 class="front-title">
        <div class="title-red">Saharan</div>
        <div class="title-white">Evacuation</div>
      </h1>
      <div class="cover-photo" role="img" aria-label="Black and white photo of a blurred hand pointing a pistol straight at the viewer"></div>
      <div class="front-author author">Marc Delorne</div>
    </div>
  </section>
</main>
</body>
</html>
```